birchwell hollow cattle company website

we would like a home page, an about us page, a page for sires, a page for dams, A sale page where we can list progreny for sale and a contact us. on the about us page we would like there to be a family picture. on the sires page we would like to have a picture of each sire, a description beside them and a link to their online profile at northern hereford registry. on the dam page we would like to have a picture of each dam, aswell as a description beside them aswell as a link to the northern hereford registry site. would like the website to very mobile phone friendly as expecting most traffic to be on phone. we would like the website to look and feel very mich like a farm, rustic, barbed wire and other farm feels. we would also like a frozen genetics pages where we can include pictures and descriptions of the sires and dams aswell as a price for embryos and semen. we need to website to be easy to maintain so we can update pictures and information as it changes, we would like there to be a feature so that people can sign up to be on our mailing list by giving us their mailing addess and email and full name
aswell as an area where they can send us a message to contact us.

leaving for work for 3 weeks in the canadian arctic will have limited ability to use the internet

Target Market(s)

other ranchers, farmers, cattlemen,

Industry/Entity Type

farming, agriculture, cattle

Coding

Coded - Design and coding required

Requirements
Must have
• about page, contact page, sires page, dams page, SALE page.
Nice to have
• country/farm vibe, barbed wire, wood,

```html
<!DOCTYPE html>
<html lang="en">
<head>
<meta charset="utf-8">
<title>Birchwell Hollow Cattle Company</title>
<link href="https://fonts.googleapis.com/css2?family=Bebas+Neue&family=Oswald:wght@500;600&family=Work+Sans:wght@400;500;600&display=swap" rel="stylesheet">
<style>
:root{
  --cream:#f2ebe0;
  --cream-light:#f7f3ec;
  --bark:#4a3426;
  --ink:#1d1915;
  --tan:#b8895a;
  --tan-text:#c08650;
  --white:#ffffff;
  --black:#0b0b0b;
  --muted:#3b3530;
}
*{margin:0;padding:0;box-sizing:border-box}
html,body{width:1200px;height:3405px;overflow:hidden}
body{background:var(--cream);font-family:"Work Sans",sans-serif;color:var(--ink);position:relative}
a{color:inherit;text-decoration:none}
.abs{position:absolute}
.display{font-family:"Bebas Neue",sans-serif;font-weight:400;letter-spacing:.5px;line-height:.95}
.label{font-family:"Oswald",sans-serif;font-weight:500;text-transform:uppercase;letter-spacing:.2px;line-height:1}
.btn{position:absolute;display:flex;align-items:center;justify-content:space-between;background:var(--tan);color:var(--white);font-family:"Oswald",sans-serif;font-weight:500;text-transform:uppercase;font-size:15px;padding:0 14px 0 13px}
.btn svg{width:18px;height:12px}
.photo{position:absolute}

.topbar{position:absolute;left:0;top:0;width:1200px;height:24px;background:var(--bark);color:var(--white);font-size:10.5px;display:flex;align-items:center;justify-content:center}
.topbar a{color:var(--tan);text-decoration:underline;margin-left:3px}

.header{position:absolute;left:0;top:24px;width:1200px;height:108px;background:var(--cream)}
.nav{position:absolute;top:48px;display:flex;gap:22px;font-size:15px}
.brand{position:absolute;left:500px;top:16px;width:200px;text-align:center;font-family:"Oswald",sans-serif;font-weight:600;color:var(--ink);text-transform:uppercase}
.brand .dot{display:block;width:34px;height:34px;border-radius:50%;background:var(--ink);margin:0 auto 6px}
.brand .n1{font-size:18px;line-height:1}
.brand .n2{font-size:9px;letter-spacing:3px;line-height:1.4}

.hero{position:absolute;left:0;top:132px;width:1200px;height:566px;overflow:hidden}
.hero .photo{inset:0;background:
  radial-gradient(ellipse 520px 260px at 560px 200px,rgba(140,64,30,.95),rgba(140,64,30,0) 70%),
  linear-gradient(180deg,#9a9088 0%,#6e5443 22%,#6b3a22 48%,#7a4a2a 66%,#a4855a 84%,#c2a774 100%)}
.hero .shade{position:absolute;inset:0;background:linear-gradient(90deg,rgba(20,12,6,.5),rgba(20,12,6,.1) 70%)}
.hero-kicker{left:122px;top:238px;color:var(--white);font-size:20px}
.hero-title{left:120px;top:260px;color:var(--white);font-size:88px}
.hero-sub{left:122px;top:346px;color:var(--white);font-size:26px}
.hero-copy{left:122px;top:390px;width:560px;color:var(--white);font-size:13px;line-height:1.45}
.scroll-badge{position:absolute;left:933px;top:344px;width:154px;height:154px}

.cat-kicker{left:0;width:1200px;text-align:center;top:742px;font-size:18px}
.cat-title{left:0;width:1200px;text-align:center;top:768px;font-size:48px}
.cat-card{position:absolute;top:835px;width:302px}
.cat-card .photo{position:relative;width:302px;height:244px;border:4px solid var(--white)}
.cat-card h3{font-size:29px;margin-top:14px}
.cat-card p{font-size:10.5px;line-height:1.55;margin-top:2px;width:290px;color:var(--muted)}

.about{position:absolute;left:0;top:1266px;width:1200px;height:875px;background:var(--cream-light);overflow:hidden}
.about .field{position:absolute;left:0;top:390px;width:1200px;height:485px;background:
  linear-gradient(180deg,rgba(247,243,236,1) 0%,#b9c0bc 14%,#6f7d68 26%,#7d8c5a 36%,#8a5436 52%,#744329 72%,#6a6a44 100%)}
.about .frame{left:122px;top:52px;width:488px;height:433px;border:4px solid var(--white);background:linear-gradient(180deg,#5c86c8 0%,#4d6f9a 12%,#2f4a2a 26%,#3c5232 40%,#7a7060 58%,#a3927a 100%)}
.ab-kicker{left:671px;top:84px;font-size:18px}
.ab-title{left:671px;top:104px;font-size:48px;line-height:.98}
.ab-lead{left:671px;top:204px;width:420px;color:var(--tan-text);font-size:13px;font-weight:600;line-height:1.45}
.ab-body{left:671px;width:420px;font-size:11.5px;line-height:1.55;color:var(--muted)}

.pa-kicker{left:122px;top:2198px;font-size:18px}
.pa-title{left:122px;top:2218px;font-size:48px}
.arrow-btn{position:absolute;top:2212px;width:48px;height:47px;display:flex;align-items:center;justify-content:center}
.arrow-btn.prev{left:975px;border:1.5px solid var(--tan);background:var(--white);color:var(--tan)}
.arrow-btn.next{left:1031px;background:var(--tan);color:var(--white)}
.animal{position:absolute;top:2287px;width:305px;height:320px;background:var(--white);padding:22px 18px}
.animal h4{font-family:"Oswald",sans-serif;font-weight:500;font-size:15px;text-transform:uppercase;line-height:1.2}
.animal .meta{font-size:11.5px;color:var(--muted);margin-top:3px}
.animal .row{font-size:10px;margin-top:9px;color:var(--muted)}
.animal .row b{font-family:"Oswald",sans-serif;font-weight:500;font-size:12px;color:var(--ink);text-transform:uppercase;margin-right:4px}
.animal .photo{position:absolute;left:18px;top:124px;width:269px;height:177px}

.bulls{position:absolute;left:0;top:2730px;width:1200px;height:396px;overflow:hidden}
.bulls .photo{inset:0;background:
  radial-gradient(ellipse 380px 170px at 320px 200px,rgba(130,70,40,.95),rgba(130,70,40,0) 75%),
  linear-gradient(180deg,#a89a74 0%,#8d7a52 30%,#8a6a42 60%,#5e5a38 100%)}
.bulls .shade{position:absolute;inset:0;background:linear-gradient(90deg,rgba(0,0,0,0) 45%,rgba(30,20,10,.45) 70%)}
.bu-kicker{left:671px;top:60px;color:var(--white);font-size:18px}
.bu-title{left:671px;top:82px;color:var(--white);font-size:48px;line-height:.94}
.bu-copy{left:671px;top:226px;width:420px;color:var(--white);font-size:12px;line-height:1.5}

.footer{position:absolute;left:0;top:3126px;width:1200px;height:279px;background:var(--black);color:var(--white)}
.footer .brand{left:122px;top:44px;width:auto;text-align:left;color:var(--white)}
.footer .brand .dot{background:var(--white);margin:0 0 6px 0}
.fcol{position:absolute;top:50px}
.fcol h5{font-family:"Oswald",sans-serif;font-weight:500;font-size:15px;text-transform:uppercase;margin-bottom:6px}
.fcol li{list-style:none;font-size:10.5px;line-height:18.5px}
.socials{position:absolute;left:886px;top:136px;display:flex;gap:10px}
.socials span{width:34px;height:34px;border-radius:50%;background:var(--tan);display:block}
.legal{position:absolute;top:246px;font-size:10px}
.legal-links{right:122px;display:flex;gap:18px}
</style>
</head>
<body>

<div class="topbar">We will post the latest information about upcoming sales here on our <a href="#">community bulletin.</a></div>

<header class="header">
  <nav class="nav label" style="left:122px">
    <a href="#">Home</a><a href="#">About Us</a><a href="#">Sires</a><a href="#">Dams</a><a href="#">For Sale</a>
  </nav>
  <a class="brand" href="#">
    <span class="dot"></span>
    <span class="n1">Birchwell Hollow</span><br>
    <span class="n2">Cattle Company</span>
  </a>
  <nav class="nav label" style="left:785px"><a href="#">Frozen Genetics</a></nav>
  <svg class="abs" style="left:901px;top:44px" width="18" height="18" viewBox="0 0 18 18" fill="none" stroke="#1d1915" stroke-width="1.8"><circle cx="7.5" cy="7.5" r="6"/><path d="M12 12l5 5"/></svg>
  <a class="btn" href="#" style="left:934px;top:37px;width:144px;height:35px">Member Log In
    <svg viewBox="0 0 18 12" fill="none" stroke="#fff" stroke-width="1.6"><path d="M1 6h15M11 1l5 5-5 5"/></svg></a>
</header>

<section class="hero">
  <div class="photo" role="img" aria-label="Red Angus bull standing in a straw-bedded corral beside metal fence panels"></div>
  <div class="shade"></div>
  <p class="abs label hero-kicker">Angus renowned for their adaptability and</p>
  <h1 class="abs display hero-title">High Performance</h1>
  <p class="abs label hero-sub">Raising quality Angus cattle with pride &amp; tradition</p>
  <p class="abs hero-copy">Lorem ipsum dolor sit amet, consectetur adipiscing elit, sed do eiusmod tempor incididunt ut labore et dolore magna aliqua.</p>
  <a class="btn" href="#" style="left:122px;top:443px;width:224px;height:48px">Request Information
    <svg viewBox="0 0 18 12" fill="none" stroke="#fff" stroke-width="1.6"><path d="M1 6h15M11 1l5 5-5 5"/></svg></a>
  <svg class="scroll-badge" viewBox="0 0 154 154">
    <defs><path id="ring" d="M77,77 m-60,0 a60,60 0 1,1 120,0 a60,60 0 1,1 -120,0"/></defs>
    <text fill="#fff" font-family="Oswald, sans-serif" font-size="10.5" letter-spacing="1.2"><textPath href="#ring">SCROLL FOR MORE. SCROLL FOR MORE. SCROLL FOR MORE. SCROLL FOR MORE.</textPath></text>
    <path d="M77 62v28M69 82l8 8 8-8" fill="none" stroke="#fff" stroke-width="2"/>
  </svg>
</section>

<p class="abs label cat-kicker">Shop by Category</p>
<h2 class="abs display cat-title">We Represent a Variety of Segments</h2>

<article class="cat-card" style="left:122px">
  <div class="photo" role="img" aria-label="Red Angus sires feeding at hay in a snowy pen" style="background:linear-gradient(180deg,#6f93b8 0%,#4f5a52 18%,#5a3a2a 38%,#3a261c 66%,#b9b4ad 86%,#dfe3e8 100%)"></div>
  <h3 class="display">Sires</h3>
  <p>Lorem ipsum dolor sit amet, consectetur adipiscing elit, sed do eiusmod tempor incididunt ut labore et dolore magna aliqua.</p>
  <a class="btn" href="#" style="left:0;top:346px;width:144px;height:34px">Explore Sires
    <svg viewBox="0 0 18 12" fill="none" stroke="#fff" stroke-width="1.6"><path d="M1 6h15M11 1l5 5-5 5"/></svg></a>
</article>
<article class="cat-card" style="left:447px">
  <div class="photo" role="img" aria-label="Hereford-cross dam standing in a dry pasture with pine hills behind" style="background:linear-gradient(180deg,#7ea5cc 0%,#48603a 20%,#5d6b3f 32%,#8a5632 52%,#a77a4a 72%,#c2a676 100%)"></div>
  <h3 class="display">Dams</h3>
  <p>Lorem ipsum dolor sit amet, consectetur adipiscing elit, sed do eiusmod tempor incididunt ut labore et dolore magna aliqua.</p>
  <a class="btn" href="#" style="left:0;top:346px;width:144px;height:34px">Explore Damss
    <svg viewBox="0 0 18 12" fill="none" stroke="#fff" stroke-width="1.6"><path d="M1 6h15M11 1l5 5-5 5"/></svg></a>
</article>
<article class="cat-card" style="left:772px">
  <div class="photo" role="img" aria-label="Group of red cattle for sale in a dirt yard below a mountain" style="background:linear-gradient(180deg,#9fb4c9 0%,#8a9088 18%,#6c7460 30%,#5a3624 52%,#6e4a34 70%,#8a7560 100%)"></div>
  <h3 class="display">Cattle Sales</h3>
  <p>Lorem ipsum dolor sit amet, consectetur adipiscing elit, sed do eiusmod tempor incididunt ut labore et dolore magna aliqua.</p>
  <a class="btn" href="#" style="left:0;top:346px;width:144px;height:34px">Progreny List
    <svg viewBox="0 0 18 12" fill="none" stroke="#fff" stroke-width="1.6"><path d="M1 6h15M11 1l5 5-5 5"/></svg></a>
</article>

<section class="about">
  <div class="field" role="img" aria-label="Herd of red and white-faced cattle along a barbed wire fence in a green valley"></div>
  <div class="photo frame" role="img" aria-label="Visitors viewing cattle in wooden corrals at a ranch sale"></div>
  <p class="abs label ab-kicker">Our Reach is Global</p>
  <h2 class="abs display ab-title">Thank You to Our Great<br>Customers!</h2>
  <p class="abs ab-lead">Lorem ipsum dolor sit amet, consectetur adipiscing elit, sed do eiusmod tempor incididunt ut labore et dolore magna aliqua.</p>
  <p class="abs ab-body" style="top:257px">Lorem ipsum dolor sit amet, consectetur adipiscing elit, sed do eiusmod tempor incididunt ut labore et dolore magna aliqua. Ut enim ad minim veniam, quis nostrud exercitation ullamco laboris nisi ut aliquip ex ea commodo consequat.</p>
  <p class="abs ab-body" style="top:346px">Duis aute irure dolor in reprehenderit in voluptate velit esse cillum dolore eu fugiat nulla pariatur. Excepteur sint occaecat cupidatat non proident, sunt in culpa qui officia deserunt mollit anim id est laborum.</p>
  <a class="btn" href="#" style="left:671px;top:410px;width:225px;height:48px">Know More About Us
    <svg viewBox="0 0 18 12" fill="none" stroke="#fff" stroke-width="1.6"><path d="M1 6h15M11 1l5 5-5 5"/></svg></a>
</section>

<p class="abs label pa-kicker">Choose from the Best</p>
<h2 class="abs display pa-title">Straight from Our Pasture</h2>
<a class="arrow-btn prev" href="#" aria-label="Previous"><svg width="18" height="12" viewBox="0 0 18 12" fill="none" stroke="currentColor" stroke-width="1.6"><path d="M17 6H2M7 1L2 6l5 5"/></svg></a>
<a class="arrow-btn next" href="#" aria-label="Next"><svg width="18" height="12" viewBox="0 0 18 12" fill="none" stroke="currentColor" stroke-width="1.6"><path d="M1 6h15M11 1l5 5-5 5"/></svg></a>

<article class="animal" style="left:122px">
  <h4>Red Birchwell Ridgeline 102L</h4>
  <p class="meta">2344994 | March 172023 | KJCB 102L</p>
  <p class="row"><b>Tattoo:</b>Tattoo: PFC105J</p>
  <p class="row" style="margin-top:6px"><b>Date of Birth:</b>February 28 2021</p>
  <div class="photo" role="img" aria-label="Red Angus calf standing on straw by a wooden fence" style="background:linear-gradient(180deg,#8a7a6a 0%,#7a6656 25%,#6a3a22 50%,#5a2e1a 68%,#c9ac78 100%)"></div>
</article>
<article class="animal" style="left:447px">
  <h4>Red Birchwell Ridgeline 102L</h4>
  <p class="meta">2344994 | March 172023 | KJCB 102L</p>
  <p class="row"><b>Tattoo:</b>Tattoo: PFC105J</p>
  <p class="row" style="margin-top:6px"><b>Date of Birth:</b>February 28 2021</p>
  <div class="photo" role="img" aria-label="Red Angus yearling bull in a wooden-fenced pen" style="background:linear-gradient(180deg,#9a8a78 0%,#7a5a44 25%,#6a3620 50%,#5c2c18 70%,#cbb488 100%)"></div>
</article>
<article class="animal" style="left:772px">
  <h4>Red Birchwell Ridgeline 102L</h4>
  <p class="meta">2344994 | March 172023 | KJCB 102L</p>
  <p class="row"><b>Tattoo:</b>Tattoo: PFC105J</p>
  <p class="row" style="margin-top:6px"><b>Date of Birth:</b>February 28 2021</p>
  <div class="photo" role="img" aria-label="Red Angus bull standing in an open field" style="background:linear-gradient(180deg,#dfe6ec 0%,#c9c2b2 22%,#a3603a 40%,#8a3e1e 65%,#c8b68e 100%)"></div>
</article>

<a class="btn" href="#" style="left:488px;top:2632px;width:224px;height:49px">Explore Our Angus
  <svg viewBox="0 0 18 12" fill="none" stroke="#fff" stroke-width="1.6"><path d="M1 6h15M11 1l5 5-5 5"/></svg></a>

<section class="bulls">
  <div class="photo" role="img" aria-label="Hereford cows grazing in tall golden grass"></div>
  <div class="shade"></div>
  <p class="abs label bu-kicker">Registered Red Angus Bulls</p>
  <h2 class="abs display bu-title">Advancing the Breed<br>with Research &amp; Breed<br>Development</h2>
  <p class="abs bu-copy">Lorem ipsum dolor sit amet, consectetur adipiscing elit, sed do eiusmod tempor incididunt ut labore et dolore magna aliqua.</p>
  <a class="btn" href="#" style="left:671px;top:272px;width:225px;height:48px">Request Information
    <svg viewBox="0 0 18 12" fill="none" stroke="#fff" stroke-width="1.6"><path d="M1 6h15M11 1l5 5-5 5"/></svg></a>
</section>

<footer class="footer">
  <a class="brand" href="#">
    <span class="dot"></span>
    <span class="n1">Birchwell Hollow</span><br>
    <span class="n2">Cattle Company</span>
  </a>
  <div class="fcol" style="left:510px">
    <h5>Quick Links</h5>
    <ul><li>Home</li><li>About Us</li><li>Our Sires</li><li>Our Dams</li><li>For Sale</li><li>Frozen Genetics</li><li>Contact</li></ul>
  </div>
  <div class="fcol" style="left:685px">
    <h5>Information</h5>
    <ul><li>Animal Inquiry</li><li>Fee Schedule</li><li>Register / Transfer an Animal</li><li>Ordering Tags</li><li>Submit Animal Weight</li></ul>
  </div>
  <div class="fcol" style="left:886px">
    <h5>Contact Us</h5>
    <ul><li>Call Us: +1 250-555-0148</li><li>Email: hello@birchwellhollow.ca</li></ul>
  </div>
  <div class="socials" aria-label="Social links"><span></span><span></span><span></span></div>
  <p class="legal" style="left:122px">© 2026 Birchwell Hollow Cattle. All Rights Reserved</p>
  <div class="legal legal-links"><a href="#">Terms and Conditions</a><a href="#">Privacy Notice</a><a href="#">Disclaimer</a></div>
</footer>

</body>
</html>
```